Harbor Crestline (Business Card Design)

Need business cards designed. Something modern, chic, and sleek. Mabye the back of the card should be the navy blue that is in the logo and then just the logo on the back.

Target Market(s)

Those in the hotel, office, and renovation industry

Contact Information for Business Card

1. Logo 2. Dorian Fenwick 3. CEO/Founder 4. Phone: (833) HarbCre / (833) 427-2731 5. Email: dorian@theharborcrestline.com 6. Website: www.theharborcrestline.com

Font styles to use
Other font styles liked:
• Look at the logo font and base the font for everything else off of that.

Colors
0054AA
0677BA
7BADD7
CADEEF
E8F1F8

Requirements
Must have
• Colors that are associated in the logo
Nice to have
• Sleek modern clean and chic design.

```html
<!DOCTYPE html>
<html lang="en">
<head>
<meta charset="utf-8">
<title>Harbor Crestline – Business Card</title>
<link href="https://fonts.googleapis.com/css2?family=Montserrat:wght@700&family=Jost:wght@400;600&display=swap" rel="stylesheet">
<style>
  :root {
    --navy: #1b2352;
    --gold: #cfa646;
    --gold-line: #e6cf98;
    --paper: #ffffff;
    --backdrop: #e3e4e6;
    --ink-soft: #4a4f63;
  }
  * { box-sizing: border-box; margin: 0; padding: 0; }
  html, body { width: 1200px; height: 800px; overflow: hidden; }
  body {
    background: var(--backdrop);
    font-family: "Jost", sans-serif;
    position: relative;
  }
  .card {
    position: absolute;
    top: 252px;
    width: 520px;
    height: 297px;
    border-radius: 3px;
    box-shadow: 0 10px 28px rgba(0,0,0,0.14);
  }
  /* Back side */
  .card-back {
    left: 50px;
    background: var(--gold);
    display: flex;
    align-items: center;
    justify-content: center;
  }
  .brand {
    display: flex;
    align-items: center;
    gap: 14px;
    color: var(--navy);
    font-family: "Montserrat", sans-serif;
    font-weight: 700;
    letter-spacing: 0.06em;
    text-transform: uppercase;
  }
  .brand-mark {
    width: 18px;
    height: 18px;
    background: var(--navy);
  }
  .card-back .brand { font-size: 30px; }
  .card-back .brand-mark { width: 22px; height: 22px; }

  /* Front side */
  .card-front {
    left: 630px;
    background: var(--paper);
  }
  .card-front .brand {
    position: absolute;
    top: 46px;
    right: 40px;
    font-size: 24px;
  }
  .card-front .brand-mark { background: var(--gold); }
  .divider {
    position: absolute;
    left: 30px;
    right: 30px;
    top: 150px;
    height: 1px;
    background: var(--gold-line);
  }
  .phones {
    position: absolute;
    left: 30px;
    top: 106px;
    list-style: none;
    font-size: 14px;
    line-height: 1.35;
    color: var(--ink-soft);
  }
  .phones li, .links li { display: flex; align-items: center; gap: 6px; }
  .person {
    position: absolute;
    left: 250px;
    top: 110px;
    color: var(--navy);
  }
  .person-name {
    font-weight: 600;
    font-size: 16px;
    letter-spacing: 0.02em;
    text-transform: uppercase;
    line-height: 1.1;
  }
  .person-title {
    font-size: 14px;
    color: var(--ink-soft);
    line-height: 1.1;
  }
  .links {
    position: absolute;
    right: 30px;
    bottom: 34px;
    list-style: none;
    font-size: 14px;
    line-height: 1.5;
    color: var(--ink-soft);
    text-align: right;
  }
  .links li { justify-content: flex-end; }
  .icon { width: 12px; height: 12px; flex: none; fill: var(--navy); }
</style>
</head>
<body>

  <section class="card card-back" aria-label="Card back">
    <div class="brand"><span class="brand-mark"></span>Harbor Crestline</div>
  </section>

  <section class="card card-front" aria-label="Card front">
    <div class="brand"><span class="brand-mark"></span>Harbor Crestline</div>

    <ul class="phones">
      <li>
        <svg class="icon" viewBox="0 0 24 24"><path d="M6.6 10.8a15 15 0 0 0 6.6 6.6l2.2-2.2c.3-.3.7-.4 1-.2 1.1.4 2.3.6 3.6.6.6 0 1 .4 1 1V20c0 .6-.4 1-1 1A17 17 0 0 1 3 4c0-.6.4-1 1-1h3.5c.6 0 1 .4 1 1 0 1.3.2 2.5.6 3.6.1.3 0 .7-.2 1z"/></svg>
        (833) HarbCre
      </li>
      <li>
        <svg class="icon" viewBox="0 0 24 24"><path d="M6.6 10.8a15 15 0 0 0 6.6 6.6l2.2-2.2c.3-.3.7-.4 1-.2 1.1.4 2.3.6 3.6.6.6 0 1 .4 1 1V20c0 .6-.4 1-1 1A17 17 0 0 1 3 4c0-.6.4-1 1-1h3.5c.6 0 1 .4 1 1 0 1.3.2 2.5.6 3.6.1.3 0 .7-.2 1z"/></svg>
        (833) 427-2731
      </li>
    </ul>

    <div class="person">
      <p class="person-name">Dorian Fenwick</p>
      <p class="person-title">CEO/Founder</p>
    </div>

    <div class="divider"></div>

    <ul class="links">
      <li>
        dorian@theharborcrestline.com
        <svg class="icon" viewBox="0 0 24 24"><path d="M2 5h20v14H2zm2 2v.5l8 5 8-5V7zm0 2.8V17h16V9.8l-8 5z"/></svg>
      </li>
      <li>
        www.theharborcrestline.com
        <svg class="icon" viewBox="0 0 24 24"><path d="M12 2a10 10 0 1 0 0 20 10 10 0 0 0 0-20zm0 2c1 0 2.2 2 2.7 5H9.3C9.8 6 11 4 12 4zM4.3 11h4.8c0 .7-.1 1.3-.1 2s0 1.3.1 2H4.3a8 8 0 0 1 0-4zm5 6h5.4c-.5 3-1.7 5-2.7 5s-2.2-2-2.7-5zm5.6-2c.1-.7.1-1.3.1-2s0-1.3-.1-2h4.8a8 8 0 0 1 0 4z"/></svg>
      </li>
    </ul>
  </section>

</body>
</html>
```